Stationery Design Project for Nimbora, Chicago

Nimbora, a street parking application which helps car drivers find a street parking spot by offering an ideal path along which to look for parking. This path is calculated by our algorithm based on data (e.g. historical data, baseball games schedule, etc.). Along this path the driver will find a spot and will also save 70% of the search time. Customer we target is reg. between 21 and 45 yo.

We envision something young, fresh, bright and original. Slightly abstract maybe. It should represent the idea and elements of finding street parking in the city, e.g. car(s), parking spot, people, city, etc. (just ideas!).

Logo is attached.

Requirement:
- Business Cards (2 Sided Full Color CMYK)
- Letterhead (1 Sided Full Color CMYK)
- Envelope (1 Sided Full Color CMYK)
- Sticker (1 Sided Full Color CMYK), round with a 2inch diameter.

Reason: We're starting to get more and more designs and need more time to look into all of them. Very exciting!! Thanks to everybody!

Hi all, we're in the process of selecting our favs. Though choices!!! Really good submissions. Will keep you posted and sorry for the delay.

Target Market(s)

Car drivers and owners between 21 and 45

Industry/Entity Type

Parking

Requirements
Must have
• Sticker should be round and include company URL nimbora.com and the new logo which we will attach soon.
Should not have
• Should not be too serious or boring.

```html
<!DOCTYPE html>
<html lang="en">
<head>
<meta charset="utf-8">
<title>Nimbora Business Cards</title>
<link rel="stylesheet" href="https://fonts.googleapis.com/css2?family=PT+Sans:wght@400;700&display=swap">
<style>
  :root {
    --backdrop: #efece4;
    --card: #ffffff;
    --ink: #2a2a2a;
    --wordmark: #1e1e1e;
    --navy: #1b3590;
    --cyan: #14b9ee;
    --icon: #1e9fdc;
    --mark: #1f5fc8;
    --white: #ffffff;
  }
  * { margin: 0; padding: 0; box-sizing: border-box; }
  html, body { width: 1200px; height: 686px; overflow: hidden; }
  body {
    background: var(--backdrop);
    font-family: "PT Sans", Arial, sans-serif;
    position: relative;
  }
  .card {
    position: absolute;
    width: 450px;
    height: 256px;
    background: var(--card);
    border-radius: 22px;
    overflow: hidden;
    box-shadow: 0 2px 6px rgba(0,0,0,0.25);
  }
  .card--front { left: 110px; top: 80px; }
  .card--back { left: 616px; top: 80px; }
  .card--sticker { left: 369px; top: 374px; }
  .card__wave { position: absolute; left: 0; top: 0; width: 450px; height: 256px; }
  .brand { position: absolute; display: flex; align-items: center; }
  .brand__dot { border-radius: 50%; background: var(--mark); flex: none; }
  .brand__name { color: var(--wordmark); font-weight: 400; line-height: 1; }
  .card--front .brand { left: 82px; top: 32px; gap: 14px; }
  .card--front .brand__dot { width: 74px; height: 74px; }
  .card--front .brand__name { font-size: 46px; }
  .card--back .brand { left: 56px; top: 61px; gap: 16px; }
  .card--back .brand__dot { width: 94px; height: 94px; }
  .card--back .brand__name { font-size: 60px; }
  .contact {
    position: absolute; left: 0; top: 124px; width: 450px;
    text-align: center; color: var(--ink); font-size: 13.5px; line-height: 21px;
  }
  .contact__row { display: flex; justify-content: center; gap: 16px; }
  .contact__item { display: inline-flex; align-items: center; gap: 3px; }
  .contact__icon { width: 12px; height: 12px; fill: var(--icon); }
  .holder {
    position: absolute; right: 46px; top: 228px;
    color: var(--white); font-weight: 700; font-size: 16px; line-height: 16px;
  }
  .holder__title { font-size: 12px; }
  .site {
    position: absolute; right: 54px; top: 230px;
    color: var(--white); font-weight: 700; font-size: 12.5px; line-height: 13px;
  }
  .sticker-mark {
    position: absolute; left: 156px; top: 66px;
    width: 138px; height: 138px; border-radius: 50%; background: var(--mark);
  }
</style>
</head>
<body>
  <svg width="0" height="0" style="position:absolute">
    <defs>
      <linearGradient id="band-blue" x1="0" x2="1" y1="0" y2="0">
        <stop offset="0" stop-color="#1b3590"/>
        <stop offset="0.6" stop-color="#14b9ee"/>
        <stop offset="1" stop-color="#1b3590"/>
      </linearGradient>
      <linearGradient id="band-dark" x1="0" x2="1" y1="0" y2="0">
        <stop offset="0" stop-color="#000"/>
        <stop offset="0.5" stop-color="#e8e8e8"/>
        <stop offset="1" stop-color="#000"/>
      </linearGradient>
      <g id="card-band">
        <path d="M0,194 C120,226 260,224 450,186 L450,199 C250,232 110,240 0,210 Z" fill="url(#band-dark)"/>
        <path d="M0,214 C100,242 230,232 450,204 L450,256 L0,256 Z" fill="url(#band-blue)"/>
      </g>
    </defs>
  </svg>

  <section class="card card--front">
    <svg class="card__wave" viewBox="0 0 450 256"><use href="#card-band"/></svg>
    <div class="brand"><span class="brand__dot"></span><span class="brand__name">Nimbora</span></div>
    <div class="contact">
      <div>Street name City, State, zip code</div>
      <div class="contact__row">
        <span class="contact__item"><svg class="contact__icon" viewBox="0 0 12 12"><path d="M3 0.5 L5 3 L3.8 4.3 C4.5 6 6 7.5 7.7 8.2 L9 7 L11.5 9 L10 11.5 C5 11 1 7 0.5 2 Z"/></svg>123-456-7890</span>
        <span class="contact__item"><svg class="contact__icon" viewBox="0 0 12 12"><path d="M3 0 H9 V4 H3 Z M0 5 H12 V10 H10 V12 H2 V10 H0 Z M3 8 V11 H9 V8 Z"/></svg>123-456-7890</span>
      </div>
      <div class="contact__row">
        <span class="contact__item"><svg class="contact__icon" viewBox="0 0 12 12"><path d="M0 2 H12 V10 H0 Z M1 3 L6 6.5 L11 3" stroke="#fff" stroke-width="1"/></svg>name@website.com</span>
        <span class="contact__item"><svg class="contact__icon" viewBox="0 0 12 12"><circle cx="6" cy="6" r="5.5"/><path d="M0.5 6 H11.5 M6 0.5 V11.5 M6 0.5 C3 3 3 9 6 11.5 M6 0.5 C9 3 9 9 6 11.5" stroke="#fff" stroke-width="0.8" fill="none"/></svg>www.website.com</span>
      </div>
    </div>
    <div class="holder">Your Name<span class="holder__title">, Title</span></div>
  </section>

  <section class="card card--back">
    <svg class="card__wave" viewBox="0 0 450 256"><use href="#card-band"/></svg>
    <div class="brand"><span class="brand__dot"></span><span class="brand__name">Nimbora</span></div>
    <div class="site">www.website.com</div>
  </section>

  <section class="card card--sticker">
    <span class="sticker-mark" role="img" aria-label="Nimbora brand mark"></span>
  </section>
</body>
</html>
```